BrimLO (Beer/Wine candles) Edgy Candle with a Cause

Help us to help others. BrimLo is a beautifully scented natural soy candle made using repurposed beer/ wine bottles while at the same time donating a portion of our profits to youth alcohol education programs. (1. Waste = Repurposed beer/wine bottle, 2.) BrimLo = (anti) drunk/alcohol 3.) Ed = education/prevention programs.)
We're looking for a design that is cool and bold yet elegant and appeals to women (90% of our customers.) No traditional beer label designs please.

The "BrimLO" logo should appear prominently in the design with the scent name (in a different font) "on top." (See the "Velvet Brimmed" poster attached.

Examples of actual scents: Amber Drift, Glowing Paloma, Fizzing Mock-ree. (None of the fragrances smell like beer/alcohol or wine.)

Also the ED in BrimeLO should stand out in some way.

The emphasis should not be on the recycling aspect, so no obvious recycling symbols.

We are open to different interpretations and have attached varying examples that we like.
Note: a "blackboard/chalkboard" label is an idea since this deals with education.

Note: files & fonts used in the final design should be editable so that we can add other scent names as needed.

Target Market(s)

Candle buyers, specifically women between the ages of 16-45

Requirements
Must have
• 1.)Free fonts or license fonts under $20.00 2.) fonts modified to look unique/original. 3.) Editable Scent name 4.) Burning instructions 5.) Warning Info
• Burning Instructions: Trim wick to 1/4" before each lighting. Keep free from foreign materials including wick trimmings. For an even burn, burn for at least 1 hour but not more than 4 hours at a time. Discontinue use when 1/4" of wax remains. Discard or recycle after use.
• Warning: Burn candle within sight. Keep out of reach of children and pets. Keep away from things that catch fire. Use with caution.
Nice to have
• Colored Scent Names
Should not have
• recycle symbols

```html
<!DOCTYPE html>
<html lang="en">
<head>
<meta charset="utf-8">
<title>BrimLO Beer Bottle Candles – Amber Drift</title>
<link rel="stylesheet" href="https://fonts.googleapis.com/css2?family=Josefin+Sans:wght@300;400;700&family=Oswald:wght@200;300&family=Kaushan+Script&family=IM+Fell+English+SC&display=swap">
<style>
  :root {
    --chalk-dark: #262626;
    --chalk-mid: #3b3b3b;
    --chalk-dust: #9a9992;
    --chalk-line: #e9e7dc;
    --chalk-soft: #c4c2b6;
    --brand-lime: #8ff12a;
    --label-mint: #6cf390;
    --label-cream: #eeecdc;
    --scent-gold: #f6b22d;
    --weight-green: #9ad62b;
  }
  * { margin: 0; padding: 0; box-sizing: border-box; }
  html, body { width: 1200px; height: 900px; overflow: hidden; background: var(--chalk-dark); }
  .label {
    position: relative;
    width: 1200px;
    height: 900px;
    overflow: hidden;
    background:
      radial-gradient(ellipse at 30% 25%, rgba(255,255,255,0.05) 0%, rgba(255,255,255,0) 40%),
      radial-gradient(ellipse at 70% 70%, rgba(255,255,255,0.04) 0%, rgba(255,255,255,0) 45%),
      radial-gradient(ellipse at 50% 45%, var(--chalk-mid) 0%, var(--chalk-dark) 80%);
    font-family: "Josefin Sans", sans-serif;
  }
  .floral-border { position: absolute; opacity: 0.55; }
  .floral-border--left { left: 0; top: 0; width: 170px; height: 900px;
    background: linear-gradient(90deg, var(--chalk-dust) 0%, rgba(154,153,146,0.35) 45%, rgba(154,153,146,0) 100%); }
  .floral-border--right { right: 0; top: 0; width: 170px; height: 900px;
    background: linear-gradient(270deg, var(--chalk-dust) 0%, rgba(154,153,146,0.35) 45%, rgba(154,153,146,0) 100%); }
  .floral-border--top { left: 0; top: 0; width: 1200px; height: 70px;
    background: linear-gradient(180deg, rgba(154,153,146,0.8) 0%, rgba(154,153,146,0) 100%); }
  .floral-border--bottom { left: 0; bottom: 0; width: 1200px; height: 110px;
    background: linear-gradient(0deg, rgba(154,153,146,0.7) 0%, rgba(154,153,146,0) 100%); }

  .brand {
    position: absolute;
    top: 70px; left: 0; width: 1200px;
    text-align: center;
    font-weight: 700;
    font-size: 150px;
    line-height: 160px;
    color: var(--brand-lime);
    letter-spacing: 2px;
  }
  .tagline {
    position: absolute;
    top: 276px; left: 0; width: 1200px;
    text-align: center;
    font-weight: 300;
    font-size: 40px;
    color: var(--chalk-soft);
    letter-spacing: 2px;
  }
  .scent-tag {
    position: absolute;
    left: 282px; top: 350px;
    width: 636px; height: 204px;
  }
  .scent-name {
    position: absolute;
    left: 320px; top: 392px; width: 558px;
    text-align: center;
    font-family: "Kaushan Script", cursive;
    font-weight: 400;
    font-size: 64px;
    line-height: 80px;
    color: var(--scent-gold);
  }
  .scent-sprig {
    position: absolute;
    left: 492px; top: 488px; width: 216px; height: 10px;
    border-radius: 5px;
    background: linear-gradient(90deg, rgba(108,243,144,0.3), var(--label-mint), rgba(108,243,144,0.3));
  }
  .product-copy {
    position: absolute;
    top: 588px; left: 0; width: 1200px;
    text-align: center;
    font-family: "Oswald", sans-serif;
    font-weight: 300;
    font-size: 23px;
    line-height: 40px;
    color: var(--chalk-line);
    text-transform: uppercase;
    letter-spacing: 1px;
  }
  .divider {
    position: absolute;
    left: 160px; top: 682px; width: 880px; height: 12px;
  }
  .cause-copy {
    position: absolute;
    top: 712px; left: 0; width: 1200px;
    text-align: center;
    font-family: "Oswald", sans-serif;
    font-weight: 300;
    font-size: 29px;
    line-height: 40px;
    color: var(--chalk-soft);
    font-variant: small-caps;
    letter-spacing: 1px;
  }
  .net-weight {
    position: absolute;
    top: 800px; left: 0; width: 1200px;
    text-align: center;
    font-family: "IM Fell English SC", serif;
    font-size: 36px;
    line-height: 40px;
    color: var(--weight-green);
  }
  .safety-copy {
    position: absolute;
    top: 846px; left: 200px; width: 800px;
    text-align: center;
    font-family: "Oswald", sans-serif;
    font-weight: 300;
    font-size: 11px;
    line-height: 15px;
    color: var(--chalk-soft);
    letter-spacing: 0.3px;
  }
  .safety-copy strong { font-weight: 300; color: var(--chalk-line); text-transform: uppercase; }
</style>
</head>
<body>
  <main class="label">
    <div class="floral-border floral-border--top" role="img" aria-label="Hand-drawn chalk flower and vine border"></div>
    <div class="floral-border floral-border--bottom" role="img" aria-label="Hand-drawn chalk flower and vine border"></div>
    <div class="floral-border floral-border--left" role="img" aria-label="Hand-drawn chalk flower and vine border"></div>
    <div class="floral-border floral-border--right" role="img" aria-label="Hand-drawn chalk flower and vine border"></div>

    <h1 class="brand">BrimLO</h1>
    <p class="tagline">beer bottle candles</p>

    <svg class="scent-tag" viewBox="0 0 636 204" aria-hidden="true">
      <rect x="20" y="20" width="596" height="164" fill="var(--label-mint)"/>
      <rect x="20" y="20" width="596" height="164" fill="none" stroke="var(--label-mint)"
            stroke-width="36" stroke-linecap="round" stroke-dasharray="0 33.1"/>
      <rect x="38" y="23" width="558" height="149" fill="var(--label-cream)"/>
    </svg>
    <h2 class="scent-name">Amber Drift</h2>
    <div class="scent-sprig" role="img" aria-label="Small leafy sprig ornament"></div>

    <p class="product-copy">High quality soy candles handcrafted from the finest<br>ingredients in repurposed/recycled beer bottles.</p>

    <svg class="divider" viewBox="0 0 880 12" aria-hidden="true">
      <line x1="4" y1="6" x2="876" y2="6" stroke="var(--chalk-line)" stroke-width="3"
            stroke-linecap="round" stroke-dasharray="12 16" opacity="0.85"/>
    </svg>

    <p class="cause-copy">Portion of the sales go to support underage<br>drinking prevention programs.</p>

    <p class="net-weight">11oz.℮311g.</p>

    <p class="safety-copy"><strong>Burning instructions:</strong> Trim wick to 1/4" before each lighting. Keep free from foreign materials including wick trimmings. Burn at least 1 hour but not more than 4 hours at a time. Discontinue use when 1/4" of wax remains. Discard or recycle after use.<br><strong>Warning:</strong> Burn candle within sight. Keep out of reach of children and pets. Keep away from things that catch fire. Use with caution.</p>
  </main>
</body>
</html>
```